Healthy lifestyle Influencer business card

I need your creativity to have a business card that I can leave in all the restaurants, hotels and spas I visit to inform them that I am an influencer specializing in the wellness sector and that I will write a review about them. You can use my instagram photos Lunavita27 or on my website www.piattileggeriorto.it. I would like my business card to impress with its creativity! thank you very much!

Contact Information for Business Card

siteweb, instagram, phone number

Font styles to use
Decorative
Script

Colors
0094D4
00A9DD
6FCCEA
C7EBF8
E9F6FB
59FF00
82FF00
B8FF75
E3FFCB
F4FFEA
FFC000
F8CF3A
FAE287
FDF2CF
FEFAEE
F0912C
F2A743
F7CA91
FBE8D2
FDF5EE
EE7325
F08F49
F5BC92
FAE3D3
FDF4ED
EB3D1F
EC4F4E
F09395
F8D3D4
FCEDEE
E54698
E96AAD
F1A4CE
F9D9EA
FCEFF6

Requirements
Nice to have
• creativity

```html
<!DOCTYPE html>
<html lang="it">
<head>
<meta charset="utf-8">
<title>Luna Vita Chef – biglietto da visita</title>
<link rel="stylesheet" href="https://fonts.googleapis.com/css2?family=Varela+Round&family=Allura&family=Roboto:wght@300&display=swap">
<style>
  :root{
    --page:#2b2b2b;
    --sage:#93b5aa;
    --sage-light:#9dbdb2;
    --sage-dark:#86a99d;
    --ink:#454545;
    --band:#4b4b4b;
    --paper:#f4f4f2;
    --contact:#f3f6f4;
  }
  *{box-sizing:border-box;margin:0;padding:0}
  html,body{width:1200px;height:1138px;overflow:hidden;background:var(--page)}
  .card{position:absolute;width:620px;height:375px;border-radius:16px;overflow:hidden}

  /* front */
  .card--front{left:272px;top:184px;background:linear-gradient(180deg,var(--sage-light),var(--sage-dark))}
  .photo{position:absolute;width:185px;height:104px;border-radius:2px}
  .photo--mousse{left:24px;top:22px;background:linear-gradient(135deg,#ece9e8,#b79a93)}
  .photo--redvelvet{left:219px;top:22px;background:linear-gradient(135deg,#d8c0b4,#c9504a)}
  .photo--berrycup{left:415px;top:22px;background:linear-gradient(135deg,#6b5a4a,#3a4d86)}
  .photo--blueberrytart{left:24px;top:135px;background:linear-gradient(180deg,#3e4656,#e4dcdc)}
  .photo--batter{left:219px;top:135px;background:linear-gradient(135deg,#8a5a2e,#c48b63)}
  .photo--coconut{left:415px;top:135px;background:linear-gradient(135deg,#f0ece8,#e2c595)}
  .front-brand{position:absolute;left:0;right:0;top:280px;text-align:center;color:var(--ink)}
  .brand-name{font-family:"Varela Round",sans-serif}
  .front-brand .brand-name{font-size:30px;line-height:36px}
  .front-brand .tagline{font-family:"Varela Round",sans-serif;font-size:13px;margin-top:6px}

  /* back */
  .card--back{left:274px;top:606px;background:var(--paper)}
  .waves{position:absolute;left:0;top:0}
  .kiwi{position:absolute;left:488px;top:0;width:132px;height:160px;border-radius:70px 0 0 80px;background:radial-gradient(ellipse at 70% 45%,#c3d86a 0,#7da63a 40%,#4f8a30 65%,#3d7a2a 100%)}
  .back-brand{position:absolute;left:22px;top:68px;color:var(--ink)}
  .back-brand .brand-name{font-size:44px;line-height:52px}
  .back-brand .tagline{font-family:"Varela Round",sans-serif;font-size:19px;margin:12px 0 0 48px}
  .person{position:absolute;left:50px;top:204px;font-family:"Allura",cursive;font-size:38px;line-height:44px;color:var(--ink)}
  .social{position:absolute;left:82px;top:254px;display:flex;align-items:center;gap:10px;font-family:"Roboto",sans-serif;font-weight:300;font-size:17px;color:var(--ink)}
  .social .dot{width:14px;height:14px;border-radius:50%;background:var(--sage-dark)}
  .contact{position:absolute;right:30px;top:273px;list-style:none;font-family:"Roboto",sans-serif;font-weight:300;font-size:17px;color:var(--contact);text-align:right}
  .contact li{display:flex;justify-content:flex-end;align-items:center;gap:12px;height:24px}
  .contact svg{width:15px;height:15px}
</style>
</head>
<body>

<section class="card card--front" aria-label="Fronte del biglietto">
  <div class="photo photo--mousse" role="img" aria-label="Foto di mousse al cioccolato in ciotola"></div>
  <div class="photo photo--redvelvet" role="img" aria-label="Foto di torta red velvet"></div>
  <div class="photo photo--berrycup" role="img" aria-label="Foto di coppa con frutti di bosco"></div>
  <div class="photo photo--blueberrytart" role="img" aria-label="Foto di crostata ai mirtilli"></div>
  <div class="photo photo--batter" role="img" aria-label="Foto di impasto in tortiera"></div>
  <div class="photo photo--coconut" role="img" aria-label="Foto di biscotti al cocco"></div>
  <div class="front-brand">
    <p class="brand-name">Luna Vita Chef</p>
    <p class="tagline">Leggeri con i piatti che ami</p>
  </div>
</section>

<section class="card card--back" aria-label="Retro del biglietto">
  <svg class="waves" width="620" height="375" viewBox="0 0 620 375" aria-hidden="true">
    <path fill="var(--sage)" d="M0,338 C120,372 250,350 380,292 C470,252 550,226 620,222 L620,375 L0,375Z"/>
    <path fill="var(--band)" d="M0,290 C70,328 190,344 290,316 C400,282 480,206 620,194 L620,212 C500,220 420,268 320,318 C220,362 90,352 0,314Z"/>
    <path fill="none" stroke="var(--band)" stroke-width="4" stroke-linecap="round" d="M50,330 C140,350 230,344 310,324"/>
  </svg>
  <div class="kiwi" role="img" aria-label="Illustrazione di kiwi a fette con foglie"></div>
  <div class="back-brand">
    <p class="brand-name">Luna Vita Chef</p>
    <p class="tagline">Leggeri con i piatti che ami</p>
  </div>
  <p class="person">Luna Verdi</p>
  <p class="social"><span class="dot"></span>@Lunavita27</p>
  <ul class="contact">
    <li>000-0000-0000
      <svg viewBox="0 0 16 16" aria-hidden="true"><path fill="currentColor" d="M2 6c0-2 3-3 6-3s6 1 6 3v1h-3V6H5v1H2zM4 8h8l1 5H3z"/></svg></li>
    <li>piattileggeriorto.it
      <svg viewBox="0 0 16 16" aria-hidden="true"><rect x="1.5" y="3.5" width="13" height="9" fill="none" stroke="currentColor"/><path d="M1.5 3.5 8 9l6.5-5.5M1.5 12.5 6 8m8.5 4.5L10 8" fill="none" stroke="currentColor"/></svg></li>
    <li>info@piattileggeriorto.it
      <svg viewBox="0 0 16 16" aria-hidden="true"><circle cx="8" cy="8" r="6.5" fill="none" stroke="currentColor"/><path d="M1.5 8h13M8 1.5c-3 3-3 10 0 13M8 1.5c3 3 3 10 0 13" fill="none" stroke="currentColor"/></svg></li>
  </ul>
</section>

</body>
</html>
```